Company or website name
- dalewintham.com
- Links to the website
- Vita Forge
- Describe your company and organization and target audience
- Founded by celebrity personal trainer and media personality Dale Wintham, Vita Forge provides high quality on-site fitness and wellness classes, and personal trainers for businesses and residential gyms throughout New York City. Our target audience are residents of high end buildings in NYC, that expect excellence and luxury
- The design should have the following
- This is a 24"x36" Poster for a complimentary event at a high end building. I would like the poster to look high end, luxury and simple and chique. The words should be clear and easy to read. It would be great to have a final copy that we can send to the printer and one which we can edit for future events Here is the text: The Halcott Spires Gym Complimentary Fitness & Wellness Event Complimentary Yoga, Pilates & Interval Training Bootcamp Classes PLUS: 30 Minute Private Training Sessions *Kids Karate Classes Also Available Saturday May 18th, 25th & June 1st Time: 9:00am - 12:15pm Halcott Spires Gym Schedule: 9:00am - 9:30am Yoga 9:45am - 10:15am Interval Training Bootcamp 11:45am -12:15pm Pilates 9:00am - 12:00pm Private Training Sessions Special Introductory Rate on Future Packages During Promotion www.Vitaforge.tv Info@vitaforge.tv
- Other Facts

```html
<!DOCTYPE html>
<html lang="en">
<head>
<meta charset="utf-8">
<title>The Halcott Spires Gym – Complimentary Fitness &amp; Wellness Event</title>
<link rel="stylesheet" href="https://fonts.googleapis.com/css2?family=Arimo:wght@400;700&display=swap">
<style>
  :root {
    --page: #ffffff;
    --white: #ffffff;
    --yellow: #f2e600;
    --rule: #e8dc1a;
    --green-top: #06140a;
    --green-mid: #1c3a12;
    --green-bottom: #4a6a1a;
    --blue-light: #2fc3dd;
    --blue-mid: #1a5a9a;
    --blue-deep: #0b1f52;
    --teal-band: #3aa0b4;
    --ribbon-warm: rgba(216, 120, 40, 0.28);
    --ribbon-cool: rgba(80, 170, 190, 0.28);
  }
  * { margin: 0; padding: 0; box-sizing: border-box; }
  html, body { width: 1200px; height: 957px; overflow: hidden; background: var(--page); }
  body { position: relative; font-family: "Arimo", Arial, sans-serif; color: var(--white); }

  .poster { position: absolute; left: 278px; top: 8px; width: 625px; height: 936px; overflow: hidden; }
  .poster-bg { position: absolute; inset: 0; }

  .athlete-photo {
    position: absolute; left: 24px; top: 128px; width: 230px; height: 800px;
    border-radius: 110px 110px 60px 60px;
    background: linear-gradient(180deg, rgba(196,150,112,0.55), rgba(150,105,75,0.5) 55%, rgba(30,30,34,0.6));
  }

  .ribbon-art {
    position: absolute; left: 262px; top: 768px; width: 350px; height: 40px;
    border-radius: 20px;
    background: linear-gradient(90deg, var(--ribbon-warm), var(--ribbon-cool));
  }

  .headline { position: absolute; right: 32px; top: 42px; text-align: right; }
  .headline__venue { font-weight: 700; font-size: 37px; line-height: 1; letter-spacing: 0.2px; }
  .headline__event { color: var(--yellow); font-weight: 400; font-size: 34px; line-height: 40px; margin-top: 6px; }

  .rule { position: absolute; left: 336px; width: 259px; height: 3px; background: var(--rule); }
  .rule--1 { top: 189px; }
  .rule--2 { top: 363px; }
  .rule--3 { top: 451px; }

  .offer { position: absolute; left: 336px; font-weight: 700; font-size: 18.5px; line-height: 21.5px; }
  .offer--classes { top: 202px; }
  .offer--plus { top: 287px; }

  .intro-rate { position: absolute; left: 336px; top: 378px; font-size: 14.5px; line-height: 20.5px; }

  .schedule { position: absolute; left: 336px; top: 477px; font-size: 14.5px; line-height: 19px; }
  .schedule__dates { font-weight: 700; margin-bottom: 7px; }
  .schedule__item { margin-bottom: 11px; }
  .schedule__name { font-weight: 700; }
  .schedule__note { margin-top: 14px; }

  .brand { position: absolute; left: 284px; top: 818px; display: flex; flex-direction: column; align-items: flex-start; }
  .brand__mark { width: 54px; height: 54px; border: 3px solid var(--white); border-radius: 50%; margin-bottom: 10px; }
  .brand__name { font-weight: 700; font-size: 11px; letter-spacing: 0.8px; text-transform: uppercase; }
  .brand__byline { font-weight: 700; font-size: 9px; letter-spacing: 0.5px; text-transform: uppercase; margin-top: 2px; }

  .contact { position: absolute; right: 36px; top: 837px; text-align: right; font-weight: 700; font-size: 18.5px; line-height: 25px; }
</style>
</head>
<body>
  <main class="poster">
    <svg class="poster-bg" width="625" height="936" viewBox="0 0 625 936" aria-hidden="true">
      <defs>
        <linearGradient id="greenField" x1="0" y1="0" x2="0.2" y2="1">
          <stop offset="0" stop-color="var(--green-top)"/>
          <stop offset="0.5" stop-color="var(--green-mid)"/>
          <stop offset="1" stop-color="var(--green-bottom)"/>
        </linearGradient>
        <linearGradient id="blueField" x1="0" y1="0" x2="0.4" y2="1">
          <stop offset="0" stop-color="var(--blue-light)"/>
          <stop offset="0.35" stop-color="var(--blue-mid)"/>
          <stop offset="1" stop-color="var(--blue-deep)"/>
        </linearGradient>
      </defs>
      <rect class="field-green" width="625" height="936" fill="url(#greenField)"/>
      <path class="band-teal" d="M88,0 L128,0 C345,250 345,640 175,936 L135,936 C300,640 300,250 88,0 Z" fill="var(--teal-band)" opacity="0.55"/>
      <path class="field-blue" d="M0,0 L100,0 C315,250 315,640 148,936 L0,936 Z" fill="url(#blueField)"/>
    </svg>

    <div class="athlete-photo" role="img" aria-label="Photo of a female athlete in black sportswear throwing a punch mid-jump"></div>

    <div class="ribbon-art" role="img" aria-label="Decorative multicolour ribbon sweeping across the poster"></div>

    <header class="headline">
      <h1 class="headline__venue">The Halcott Spires Gym</h1>
      <p class="headline__event">Complimentary Fitness<br>&amp; Wellness Event</p>
    </header>

    <div class="rule rule--1"></div>
    <p class="offer offer--classes">Complimentary Yoga<br>Pilates &amp; Interval Training<br>Bootcamp Classes</p>
    <p class="offer offer--plus">PLUS FREE:<br>30 Minutes Private<br>Training Sessions</p>
    <div class="rule rule--2"></div>
    <p class="intro-rate">Special Introductory Rate<br>on Future Packages<br>During Promotion</p>
    <div class="rule rule--3"></div>

    <section class="schedule">
      <p class="schedule__dates">Saturday May 18th, 25th &amp; June 1st</p>
      <p class="schedule__item"><span class="schedule__name">Yoga</span><br>9:00am - 9:30am</p>
      <p class="schedule__item"><span class="schedule__name">Interval Training Bootcamp</span><br>9:45am - 10:15am</p>
      <p class="schedule__item"><span class="schedule__name">Pilates</span><br>11:45am - 12:15pm</p>
      <p class="schedule__item"><span class="schedule__name">Complimentary Personal Training</span><br>9:00am - 12:00pm</p>
      <p class="schedule__note">*Kids Karate Classes Also Available</p>
    </section>

    <div class="brand">
      <span class="brand__mark"></span>
      <span class="brand__name">Vita Forge</span>
      <span class="brand__byline">by Dale Wintham</span>
    </div>

    <p class="contact">www.vitaforge.tv<br>info@vitaforge.tv</p>
  </main>
</body>
</html>
```